Corvane Business Cards

Front of business card will have logo, name, address, & telephone number. Back of card will have a list of services provided - Roads, Substation Pads, Temporary Pads, Site Pads, Land Leveling, Powerline Row Cleaning, Land Clearing, Gates, Fencing, Construction Entrances, Excavation, Trenching, Underground Utilities, Directional Boring, Pile Driving. We are a construction company that uses heavy equipment like bulldozers, motor graders/blades, dump trucks, backhoes, hydro axes, & skid loaders. We build roads, pads, & install electric utility lines & waterlines underground. This logo is new. The word "Construction" can be smaller as uploaded 2 example edited logos. We will be using this card design for many employees.
Target Market(s)
Industrial Electric Powerline, Wind Turbine, Solar Panel, & Water Utility companies.
Contact Information for Business Card
Name/Position - Dwayne Halster - Owner
Address: 4875 FM 309
Merkel, TX 79412
Phone number - (325) 482-5096

```html
<!DOCTYPE html>
<html lang="en">
<head>
<meta charset="utf-8">
<title>Corvane Construction — Business Cards</title>
<link rel="stylesheet" href="https://fonts.googleapis.com/css2?family=Archivo+Black&family=Arimo:wght@400;700&display=swap">
<style>
  :root {
    --canvas: #e9e7e6;
    --maroon: #3b1219;
    --maroon-deep: #2e0d13;
    --paper: #ffffff;
    --ink: #1c1c1c;
    --phone-grey: #3d3d3d;
    --rule: #8a8a8a;
    --rule-light: rgba(255,255,255,0.35);
  }
  * { box-sizing: border-box; margin: 0; padding: 0; }
  html, body {
    width: 1200px;
    height: 1108px;
    overflow: hidden;
    background: var(--canvas);
  }
  .sheet {
    position: relative;
    width: 1200px;
    height: 1108px;
    display: flex;
    justify-content: center;
    align-items: center;
    gap: 64px;
  }
  .card {
    width: 440px;
    height: 770px;
    border-radius: 26px;
    display: flex;
    flex-direction: column;
    align-items: center;
    text-align: center;
    box-shadow: 0 6px 18px rgba(0,0,0,0.12);
    overflow: hidden;
  }

  /* Front */
  .card--front {
    background: var(--paper);
    padding-top: 150px;
  }
  .brand {
    display: flex;
    align-items: center;
    gap: 14px;
    color: var(--maroon);
    font-family: "Archivo Black", sans-serif;
  }
  .brand__mark {
    width: 22px;
    height: 22px;
    background: var(--maroon);
  }
  .brand__name {
    font-size: 56px;
    line-height: 1;
    letter-spacing: 1px;
  }
  .brand__sub {
    margin-top: 14px;
    font-family: "Archivo Black", sans-serif;
    color: var(--maroon);
    font-size: 26px;
    letter-spacing: 2px;
  }
  .person__name {
    margin-top: 58px;
    font-family: "Archivo Black", sans-serif;
    color: var(--maroon);
    font-size: 34px;
    line-height: 1.05;
  }
  .person__role {
    margin-top: 4px;
    font-family: "Arimo", sans-serif;
    font-size: 22px;
    color: var(--ink);
  }
  .rule {
    width: 150px;
    height: 1px;
    background: var(--rule);
    margin: 16px 0;
  }
  .phone {
    font-family: "Archivo Black", sans-serif;
    font-size: 28px;
    color: var(--phone-grey);
    letter-spacing: 1px;
  }
  .address {
    font-family: "Arimo", sans-serif;
    font-size: 25px;
    line-height: 1.2;
    color: var(--ink);
    font-style: normal;
  }

  /* Back */
  .card--back {
    background: linear-gradient(160deg, var(--maroon) 0%, var(--maroon-deep) 100%);
    color: var(--paper);
    padding-top: 300px;
    font-family: "Arimo", sans-serif;
  }
  .back-brand {
    display: flex;
    align-items: center;
    gap: 8px;
    font-family: "Archivo Black", sans-serif;
    font-size: 26px;
    color: var(--paper);
  }
  .back-brand__mark {
    width: 12px;
    height: 12px;
    background: var(--paper);
  }
  .services {
    margin-top: 84px;
    font-size: 21px;
    line-height: 1.22;
    padding: 0 40px;
  }
  .services__rule {
    width: 240px;
    height: 1px;
    background: var(--rule-light);
    margin: 14px auto;
  }
</style>
</head>
<body>
<main class="sheet">
  <section class="card card--front" aria-label="Business card front">
    <div class="brand">
      <span class="brand__mark" aria-hidden="true"></span>
      <span class="brand__name">CORVANE</span>
    </div>
    <div class="brand__sub">CONSTRUCTION</div>
    <h1 class="person__name">DWAYNE HALSTER</h1>
    <p class="person__role">Owner</p>
    <div class="rule"></div>
    <p class="phone">(555) 482-5096</p>
    <div class="rule"></div>
    <address class="address">4875 FM 309<br>Halvern, TX 79412</address>
  </section>

  <section class="card card--back" aria-label="Business card back">
    <div class="back-brand">
      <span class="back-brand__mark" aria-hidden="true"></span>
      <span>CORVANE</span>
    </div>
    <div class="services">
      <p>We are a construction company that uses heavy equipment like bulldozers | motor graders/blades dump trucks | backhoes hydro axes &amp; skid loaders.</p>
      <div class="services__rule"></div>
      <p>We build roads, pads install electric utility lines waterlines underground.</p>
    </div>
  </section>
</main>
</body>
</html>
```